Redesign of the UI of a customer service platform

To improve the user experience of our customers, we need a new design for our agent interface of our customer service platform (velorant.com).
The focus will be on the dashboard and the inbox screens (see attached) along with the common UI elements (Buttons, menu, fonts, forms...)
We want a simple and distinctive design

Target Market(s)

Worldwide

Industry/Entity Type

It Service

Number of Pages Required

3 page

Font styles to use
Sans Serif

Requirements
Must have
• New Onboarding page: this is a new page that is shown to user the first time they login to the platform. This will replace the current onboarding screen (setup SMS, Setup widget...etc)
• Dashboard page: to access important information and activate services (see screenshot from current site)
• Inbox page: to manage all the interactions with customers. (see screenshot from current site)
• UI elements (buttons, menus, forms, tables, fonts, color palette)

```html
<!DOCTYPE html>
<html lang="en">
<head>
<meta charset="utf-8">
<title>Quillreach Agent Inbox</title>
<link rel="stylesheet" href="https://fonts.googleapis.com/css2?family=Open+Sans:wght@300;400;600&display=swap">
<style>
:root{
  --brand:#f0542a;
  --nav-bg:#ffffff;
  --nav-active:#f5f0ed;
  --icon:#a3a3a3;
  --label:#7b7b7b;
  --canvas:#f5f0ed;
  --sidebar-head:#4a4441;
  --line:#e3e0de;
  --text:#3d3d3d;
  --muted:#8a8a8a;
  --link:#e8452a;
  --bubble:#e3f2f8;
  --badge-orange:#f9a825;
  --badge-teal:#3bbfc7;
  --close-green:#8fd69a;
  --online:#3fc24a;
  --avatar-a:#c9b7a6;
  --avatar-b:#b79f8c;
}
*{box-sizing:border-box;margin:0;padding:0}
html,body{width:1200px;height:831px;overflow:hidden;background:var(--canvas)}
body{font-family:"Open Sans",sans-serif;color:var(--text)}
.app{position:absolute;left:0;top:0;width:1300px;height:900px;transform:scale(.923077);transform-origin:0 0;background:var(--canvas)}
.avatar{position:absolute;border-radius:50%;background:radial-gradient(circle at 50% 40%,var(--avatar-a),var(--avatar-b));}
.topbar{position:absolute;left:0;top:0;width:1300px;height:90px;background:var(--nav-bg);border-bottom:1px solid var(--line)}
.brand{position:absolute;left:0;top:0;width:90px;height:90px;background:var(--brand);color:#fff;font-weight:600;font-size:14px;display:flex;align-items:center;justify-content:center}
.nav-item{position:absolute;top:0;width:91px;height:90px;border-right:1px solid var(--line);text-align:center;color:var(--label);font-size:14px}
.nav-item.is-active{background:var(--nav-active)}
.nav-item svg{position:absolute;left:30px;top:16px}
.nav-item span.label{position:absolute;left:0;right:0;top:55px}
.badge{position:absolute;top:19px;width:24px;height:24px;border-radius:50%;color:#fff;font-size:13px;line-height:24px;font-weight:600}
.badge.orange{background:var(--badge-orange);left:56px}
.badge.teal{background:var(--badge-teal);left:55px}
.online{position:absolute;left:1222px;top:16px;width:14px;height:14px;border-radius:50%;background:var(--online);z-index:2}
.sidebar{position:absolute;left:0;top:90px;width:372px;height:810px;background:#fff;border-right:1px solid var(--line)}
.sidebar-head{height:89px;background:var(--sidebar-head);color:#fff;text-align:center;padding-top:20px;position:relative}
.sidebar-head h2{font-weight:400;font-size:19px}
.sidebar-head p{font-size:13px;font-weight:600;margin-top:2px}
.sidebar-head svg{position:absolute;right:15px;top:38px}
.conv{position:relative;height:91px;border-bottom:1px solid var(--line);background:#fff}
.conv.is-selected{background:var(--nav-active)}
.conv .name{position:absolute;left:90px;top:24px;font-size:17px;color:var(--text)}
.conv .preview{position:absolute;left:90px;top:52px;font-size:13.5px;color:var(--muted);display:flex;gap:6px;align-items:center;white-space:nowrap}
.conv .time{position:absolute;right:14px;top:13px;font-size:11.5px;color:var(--muted)}
.panel{position:absolute;top:105px;height:779px;background:#fff}
.profile{left:388px;width:445px}
.chat{left:839px;width:445px}
.btn{position:absolute;top:16px;height:25px;border-radius:2px;font-size:14px;display:flex;align-items:center;gap:6px;padding:0 10px}
.btn-close{left:233px;background:var(--close-green);color:#fff}
.btn-transfer{left:320px;background:#f1eeec;color:#8d8d8d}
.kebab{position:absolute;width:4px}
.kebab i{display:block;width:4px;height:4px;border-radius:50%;background:#aaa;margin-bottom:3px}
.cust-name{position:absolute;left:0;right:0;top:203px;text-align:center;font-size:17px}
.cust-meta{position:absolute;left:0;right:0;top:238px;display:flex;justify-content:center;gap:14px;font-size:14px;color:var(--muted);align-items:center}
.cust-meta span{display:flex;gap:6px;align-items:center}
.divider{position:absolute;left:14px;right:14px;height:1px;background:var(--line)}
.section-title{position:absolute;left:13px;font-size:17px}
.add{position:absolute;right:14px;font-size:13.5px;color:var(--muted)}
.detail{position:absolute;left:0;width:445px;font-size:13.5px;height:20px}
.detail .k{position:absolute;right:335px;color:var(--muted);white-space:nowrap}
.detail .v{position:absolute;left:131px;color:var(--muted)}
.detail .v.link{color:var(--link)}
.detail svg{position:absolute;left:414px;top:2px}
.show-all{position:absolute;left:0;right:0;top:519px;text-align:center;color:var(--link);font-size:13.5px}
.task{position:absolute;left:13px;width:420px;font-size:13.5px;color:var(--muted)}
.task .date{position:absolute;left:268px}
.task svg{position:absolute;top:2px}
.empty{position:absolute;left:0;right:0;top:744px;text-align:center;font-size:13.5px;color:var(--muted)}
.bubble{position:absolute;background:var(--bubble);color:#6e6e6e;font-size:13.5px;line-height:22px;padding:5px 10px;border-radius:2px;white-space:nowrap}
.stamp{position:absolute;font-size:11.5px;color:var(--muted)}
.composer-line{position:absolute;left:14px;right:14px;top:685px;height:1px;background:var(--line)}
.composer{position:absolute;left:15px;top:703px;font-size:14px;color:var(--muted)}
.tools{position:absolute;right:14px;top:655px;display:flex;gap:8px}
</style>
</head>
<body>
<div class="app">

  <header class="topbar">
    <div class="brand">quillreach</div>
    <nav>
      <div class="nav-item is-active" style="left:90px">
        <svg width="30" height="26" viewBox="0 0 30 26"><path d="M2 14l5-9h16l5 9v10H2z" fill="var(--icon)"/><path d="M2 14h8l2 4h6l2-4h8" fill="none" stroke="#fff" stroke-width="2"/></svg>
        <span class="badge orange">4</span><span class="label">Inbox</span>
      </div>
      <div class="nav-item" style="left:182px">
        <svg width="26" height="28" viewBox="0 0 26 28"><rect x="3" y="2" width="20" height="24" rx="2" fill="none" stroke="var(--icon)" stroke-width="2.5"/><path d="M7 9h12M7 14h12M7 19h7" stroke="var(--icon)" stroke-width="2"/></svg>
        <span class="badge teal">1</span><span class="label">Tasks</span>
      </div>
      <div class="nav-item" style="left:273px">
        <svg width="30" height="28" viewBox="0 0 30 28"><circle cx="15" cy="8" r="6.5" fill="var(--icon)"/><path d="M4 27c0-7 5-11 11-11s11 4 11 11z" fill="var(--icon)"/></svg>
        <span class="label">Customers</span>
      </div>
      <div class="nav-item" style="left:364px">
        <svg width="32" height="26" viewBox="0 0 32 26"><path d="M2 3l28 10L2 23l5-10z" fill="none" stroke="var(--icon)" stroke-width="2" stroke-linejoin="round"/><path d="M7 13h23" stroke="var(--icon)" stroke-width="2"/></svg>
        <span class="label">Campaigns</span>
      </div>
      <div class="nav-item" style="left:455px">
        <svg width="30" height="28" viewBox="0 0 30 28"><text x="15" y="24" text-anchor="middle" font-family="Open Sans,sans-serif" font-size="26" fill="var(--icon)">$</text></svg>
        <span class="label">Payments</span>
      </div>
      <div class="nav-item" style="left:546px">
        <svg width="30" height="28" viewBox="0 0 30 28"><path d="M4 2v25M11 8v19M18 2v25M25 12v15" stroke="var(--icon)" stroke-width="3"/></svg>
        <span class="label">Reports</span>
      </div>
      <div class="nav-item" style="left:637px">
        <svg width="30" height="28" viewBox="0 0 30 28"><circle cx="15" cy="14" r="9" fill="none" stroke="var(--icon)" stroke-width="6" stroke-dasharray="4 3"/><circle cx="15" cy="14" r="7" fill="var(--icon)"/><circle cx="15" cy="14" r="3" fill="#fff"/></svg>
        <span class="label">Settings</span>
      </div>
    </nav>
    <span class="online"></span>
    <div class="avatar" role="img" aria-label="Agent profile photo" style="left:1226px;top:15px;width:60px;height:60px"></div>
  </header>

  <aside class="sidebar">
    <div class="sidebar-head">
      <h2>Open Conversations</h2>
      <p>New or Assigned to me</p>
      <svg width="14" height="9" viewBox="0 0 14 9"><path d="M1 1l6 6 6-6" fill="none" stroke="#fff" stroke-width="2"/></svg>
    </div>
    <div class="conv">
      <div class="avatar" role="img" aria-label="Customer photo" style="left:15px;top:16px;width:60px;height:60px"></div>
      <span class="name">Lena Morrow</span><span class="time">2 mins ago</span>
      <span class="preview"><svg width="14" height="12" viewBox="0 0 14 12"><path d="M0 5l14-5-4 12-3-5z" fill="#aaa"/></svg>Yes that would be great, please…</span>
      <div class="avatar" role="img" aria-label="Agent photo" style="left:330px;top:33px;width:28px;height:28px"></div>
    </div>
    <div class="conv is-selected">
      <div class="avatar" role="img" aria-label="Customer photo" style="left:15px;top:16px;width:60px;height:60px"></div>
      <span class="name">Owen Harlow</span><span class="time">9 mins ago</span>
      <span class="preview"><svg width="14" height="12" viewBox="0 0 14 12"><rect x="1" y="1" width="12" height="8" fill="#aaa"/><path d="M4 11h6" stroke="#aaa" stroke-width="2"/></svg>Hi, I need to know if there are…</span>
      <div class="avatar" role="img" aria-label="Agent photo" style="left:330px;top:33px;width:28px;height:28px"></div>
    </div>
    <div class="conv">
      <div class="avatar" role="img" aria-label="Customer photo" style="left:15px;top:16px;width:60px;height:60px"></div>
      <span class="name">Paul Dresner</span><span class="time">1 mins ago</span>
      <span class="preview"><svg width="8" height="13" viewBox="0 0 8 13"><circle cx="4" cy="4" r="3" fill="#aaa"/><rect x="3" y="6" width="2" height="7" fill="#aaa"/></svg>The issue occured one more…</span>
      <div class="avatar" role="img" aria-label="Agent photo" style="left:330px;top:33px;width:28px;height:28px"></div>
    </div>
    <div class="conv">
      <div class="avatar" role="img" aria-label="Customer photo" style="left:15px;top:16px;width:60px;height:60px"></div>
      <span class="name">Owen Harlow</span><span class="time">2 mins ago</span>
      <span class="preview"><svg width="14" height="12" viewBox="0 0 14 12"><path d="M6 1L1 6l5 5V8c4 0 6 1 8 3-1-4-3-7-8-7z" fill="#aaa"/></svg>Yes that's true we are not…</span>
      <div class="avatar" role="img" aria-label="Agent photo" style="left:297px;top:33px;width:28px;height:28px"></div>
      <div class="avatar" role="img" aria-label="Agent photo" style="left:330px;top:33px;width:28px;height:28px"></div>
    </div>
    <div class="conv">
      <div class="avatar" role="img" aria-label="Customer photo" style="left:15px;top:16px;width:60px;height:60px"></div>
      <span class="name">Lena Morrow</span><span class="time">3 mins ago</span>
      <span class="preview"><svg width="14" height="12" viewBox="0 0 14 12"><path d="M0 5l14-5-4 12-3-5z" fill="#aaa"/></svg>Yes that would be great, please…</span>
      <div class="avatar" role="img" aria-label="Agent photo" style="left:330px;top:33px;width:28px;height:28px"></div>
    </div>
  </aside>

  <section class="panel profile">
    <span class="btn btn-close"><svg width="14" height="11" viewBox="0 0 14 11"><path d="M1 5l4 4 8-8" fill="none" stroke="#fff" stroke-width="2.5"/></svg>Close</span>
    <span class="btn btn-transfer"><svg width="12" height="11" viewBox="0 0 12 11"><path d="M0 5.5h9M5 1l5 4.5L5 10" fill="none" stroke="#999" stroke-width="2"/></svg>Transfer</span>
    <div class="kebab" style="left:427px;top:20px"><i></i><i></i><i></i></div>
    <div class="avatar" role="img" aria-label="Customer portrait" style="left:164px;top:72px;width:118px;height:118px"></div>
    <div class="cust-name">Owen Harlow</div>
    <div class="cust-meta">
      <span><svg width="16" height="13" viewBox="0 0 16 13"><rect x="1" y="1" width="14" height="9" fill="#aaa"/><path d="M5 12h6" stroke="#aaa" stroke-width="2"/></svg>Campaigns</span>
      <span><svg width="11" height="15" viewBox="0 0 11 15"><path d="M5.5 0A5.5 5.5 0 0 0 0 5.5C0 9 5.5 15 5.5 15S11 9 11 5.5A5.5 5.5 0 0 0 5.5 0z" fill="#aaa"/><circle cx="5.5" cy="5.5" r="2" fill="#fff"/></svg>United States</span>
    </div>
    <div class="divider" style="top:286px"></div>
    <div class="section-title" style="top:304px">Details</div>
    <div class="add" style="top:307px">+ ADD</div>

    <div class="detail" style="top:351px"><span class="k">#ID :</span><span class="v">41</span><svg width="15" height="15" viewBox="0 0 15 15"><path d="M2 13l1-4 8-8 3 3-8 8z" fill="#bbb"/></svg></div>
    <div class="detail" style="top:377px"><span class="k">Email :</span><span class="v link">owen.harlow@mailbay.com</span><svg width="15" height="15" viewBox="0 0 15 15"><path d="M2 13l1-4 8-8 3 3-8 8z" fill="#bbb"/></svg></div>
    <div class="detail" style="top:403px"><span class="k">Phone :</span><span class="v link">+1(555)010 0364</span><svg width="15" height="15" viewBox="0 0 15 15"><path d="M2 13l1-4 8-8 3 3-8 8z" fill="#bbb"/></svg></div>
    <div class="detail" style="top:429px"><span class="k">Address Line 1 :</span><span class="v">48 Juniper Hollow Road</span><svg width="15" height="15" viewBox="0 0 15 15"><path d="M2 13l1-4 8-8 3 3-8 8z" fill="#bbb"/></svg></div>
    <div class="detail" style="top:455px"><span class="k">City :</span><span class="v">Durham</span><svg width="15" height="15" viewBox="0 0 15 15"><path d="M2 13l1-4 8-8 3 3-8 8z" fill="#bbb"/></svg></div>
    <div class="detail" style="top:481px"><span class="k">State :</span><span class="v">North Carolina</span><svg width="15" height="15" viewBox="0 0 15 15"><path d="M2 13l1-4 8-8 3 3-8 8z" fill="#bbb"/></svg></div>
    <div class="show-all"><svg width="11" height="8" viewBox="0 0 11 8"><path d="M1 1l4.5 4.5L10 1" fill="none" stroke="var(--link)" stroke-width="1.6"/></svg> Show All</div>

    <div class="divider" style="top:554px"></div>
    <div class="section-title" style="top:570px">Tasks</div>
    <div class="add" style="top:573px">+ ADD</div>
    <div class="task" style="top:612px">Verify customer identity<span class="date">2017-15-01</span>
      <svg style="left:357px" width="16" height="13" viewBox="0 0 16 13"><path d="M1 7l4 4 10-10" fill="none" stroke="#bbb" stroke-width="2.2"/></svg>
      <svg style="left:406px" width="13" height="15" viewBox="0 0 13 15"><path d="M1 3h11M4 3V1h5v2" stroke="#bbb" stroke-width="1.6" fill="none"/><path d="M2 4h9l-1 11H3z" fill="#bbb"/></svg>
    </div>
    <div class="task" style="top:638px">Check if the customer was billed twice<span class="date">2017-16-01</span>
      <svg style="left:357px" width="16" height="13" viewBox="0 0 16 13"><path d="M1 7l4 4 10-10" fill="none" stroke="#bbb" stroke-width="2.2"/></svg>
      <svg style="left:383px" width="13" height="13" viewBox="0 0 13 13"><path d="M1 1l11 11M12 1L1 12" stroke="#bbb" stroke-width="1.8"/></svg>
      <svg style="left:406px" width="13" height="15" viewBox="0 0 13 15"><path d="M1 3h11M4 3V1h5v2" stroke="#bbb" stroke-width="1.6" fill="none"/><path d="M2 4h9l-1 11H3z" fill="#bbb"/></svg>
    </div>

    <div class="divider" style="top:685px"></div>
    <div class="section-title" style="top:701px">Notes</div>
    <div class="add" style="top:704px">+ ADD</div>
    <div class="empty">Empty</div>
  </section>

  <section class="panel chat">
    <div class="kebab" style="left:427px;top:20px"><i></i><i></i><i></i></div>

    <div class="avatar" role="img" aria-label="Customer photo" style="left:15px;top:41px;width:60px;height:60px"></div>
    <div class="bubble" style="left:91px;top:47px;padding:2px 10px">Hello</div>
    <div class="bubble" style="left:91px;top:74px;width:262px">My CC got billed twice on subscription<br>renewal!</div>

    <div class="avatar" role="img" aria-label="Agent photo" style="left:371px;top:181px;width:60px;height:60px"></div>
    <div class="bubble" style="right:92px;top:186px;padding:2px 10px">Hi Owen</div>
    <div class="bubble" style="right:92px;top:213px;width:262px">Cay you please give me the last four<br>digits of your CC?</div>
    <div class="bubble" style="right:92px;top:268px;padding:2px 10px">I need that for verification purposes</div>

    <div class="avatar" role="img" aria-label="Customer photo" style="left:15px;top:350px;width:60px;height:60px"></div>
    <div class="bubble" style="left:91px;top:355px;padding:2px 10px">Ok, here you go 5411</div>

    <div class="avatar" role="img" aria-label="Agent photo" style="left:371px;top:435px;width:60px;height:60px"></div>
    <div class="bubble" style="right:92px;top:441px;padding:2px 10px">I will let billing know about this</div>

    <div class="avatar" role="img" aria-label="Customer photo" style="left:15px;top:521px;width:60px;height:60px"></div>
    <div class="bubble" style="left:91px;top:527px;width:262px">Yes that would be great, please do this<br>ASAP</div>
    <div class="stamp" style="left:91px;top:583px">2 mins ago</div>

    <div class="tools">
      <svg width="12" height="16" viewBox="0 0 12 16"><text x="6" y="14" text-anchor="middle" font-family="Open Sans,sans-serif" font-size="16" fill="#aaa">$</text></svg>
      <svg width="12" height="16" viewBox="0 0 12 16"><path d="M8 4v7a2.5 2.5 0 0 1-5 0V3a1.7 1.7 0 0 1 3.4 0v8" fill="none" stroke="#aaa" stroke-width="1.4"/></svg>
      <svg width="16" height="16" viewBox="0 0 16 16"><rect x="1" y="2" width="14" height="12" fill="none" stroke="#aaa" stroke-width="1.6"/><path d="M2 13l4-5 3 3 2-2 3 4z" fill="#aaa"/></svg>
      <svg width="16" height="16" viewBox="0 0 16 16"><circle cx="8" cy="8" r="7" fill="none" stroke="#aaa" stroke-width="1.5"/><circle cx="5.5" cy="6.5" r="1" fill="#aaa"/><circle cx="10.5" cy="6.5" r="1" fill="#aaa"/><path d="M4.5 9.5a3.5 3.5 0 0 0 7 0" fill="none" stroke="#aaa" stroke-width="1.4"/></svg>
    </div>
    <div class="composer-line"></div>
    <div class="composer">Your Message...</div>
  </section>

</div>
</body>
</html>
```